Business Card for Professional Photographer

I'm looking for an eye catching modern clean design that compliments my logo/ website fonts & colours.
I specialise in architecture, corporate & commercial photography so I'm marketing to professional clients rather than portrait / wedding clients.

I would prefer to not have a solid black design.

My logo brand guide is as follows :

Main front font. : Reislust
Main font colour : #fff
Slogan front font : Ubuntu Bold
Monogram front font : Venti Medium
Container colour : #fff

I need print ready files in pdf .png & .eps formats.

Included in the files below are some screen grabs as reference to font & colours etc.

```html
<!DOCTYPE html>
<html lang="en">
<head>
<meta charset="utf-8">
<title>Quiet Frame – Business Card</title>
<link rel="stylesheet" href="https://fonts.googleapis.com/css2?family=Open+Sans:wght@300;400;700&display=swap">
<style>
  :root {
    --backdrop: #2f2a27;
    --card: #262627;
    --gold: #cfa64e;
    --white: #f4f4f4;
    --muted: #d9d9d9;
  }
  * { margin: 0; padding: 0; box-sizing: border-box; }
  html, body { width: 1200px; height: 847px; overflow: hidden; }
  body {
    background: var(--backdrop);
    font-family: "Open Sans", sans-serif;
    display: flex;
    align-items: center;
    justify-content: center;
    gap: 40px;
  }
  .card {
    position: relative;
    width: 540px;
    height: 309px;
    background: var(--card);
    border-radius: 3px;
    box-shadow: 0 10px 24px rgba(0,0,0,.35);
  }
  /* back face */
  .card--back { display: flex; align-items: center; justify-content: center; gap: 14px; }
  .back-mark__dot { width: 14px; height: 14px; border-radius: 50%; background: var(--gold); }
  .back-mark__name {
    color: var(--gold); font-weight: 400; font-size: 26px;
    letter-spacing: 6px; text-transform: uppercase;
  }
  /* front face */
  .brand { position: absolute; left: 120px; top: 62px; display: flex; align-items: center; gap: 14px; }
  .brand__dot { width: 12px; height: 12px; border-radius: 50%; background: var(--gold); }
  .brand__name {
    color: var(--white); font-weight: 300; font-size: 22px;
    letter-spacing: 6px; text-transform: uppercase; line-height: 1;
  }
  .brand__slogan {
    display: block; margin-top: 6px; color: var(--gold);
    font-size: 8px; font-weight: 700; letter-spacing: 2.6px;
  }
  .person { position: absolute; right: 310px; top: 178px; text-align: right; }
  .person__name { color: var(--gold); font-weight: 700; font-size: 22px; letter-spacing: -.3px; text-transform: uppercase; }
  .person__role { color: var(--white); font-size: 13px; margin-top: 2px; }
  .divider { position: absolute; left: 246px; top: 178px; width: 1px; height: 64px; background: var(--gold); }
  .contacts { position: absolute; left: 262px; top: 176px; list-style: none; }
  .contacts__item {
    display: flex; align-items: center; gap: 6px;
    color: var(--white); font-size: 14px; line-height: 22px;
  }
  .contacts__icon { width: 11px; height: 11px; fill: var(--gold); flex: none; }
</style>
</head>
<body>
  <section class="card card--back" aria-label="Card back">
    <span class="back-mark__dot"></span>
    <span class="back-mark__name">Quiet Frame</span>
  </section>

  <section class="card card--front" aria-label="Card front">
    <div class="brand">
      <span class="brand__dot"></span>
      <div>
        <span class="brand__name">Quiet Frame</span>
        <span class="brand__slogan">Architecture Corporate Commercial</span>
      </div>
    </div>

    <div class="person">
      <p class="person__name">Daniel Harrow</p>
      <p class="person__role">Director</p>
    </div>

    <span class="divider"></span>

    <ul class="contacts">
      <li class="contacts__item">
        <svg class="contacts__icon" viewBox="0 0 24 24"><path d="M6.6 10.8a15.1 15.1 0 0 0 6.6 6.6l2.2-2.2c.3-.3.7-.4 1-.2 1.1.4 2.3.6 3.6.6.6 0 1 .4 1 1V20c0 .6-.4 1-1 1A17 17 0 0 1 3 4c0-.6.4-1 1-1h3.5c.6 0 1 .4 1 1 0 1.3.2 2.5.6 3.6.1.3 0 .7-.2 1z"/></svg>
        555 014 2680
      </li>
      <li class="contacts__item">
        <svg class="contacts__icon" viewBox="0 0 24 24"><path d="M2 5h20v14H2z M2 5l10 8 10-8" fill="none" stroke="currentColor" style="stroke:var(--gold)" stroke-width="0"/><path d="M2 5h20v2l-10 7L2 7z M2 9l10 7 10-7v10H2z"/></svg>
        hello@quietframe.com
      </li>
      <li class="contacts__item">
        <svg class="contacts__icon" viewBox="0 0 24 24"><circle cx="12" cy="12" r="10" fill="none" stroke-width="2.4" style="stroke:var(--gold)"/><path d="M2 12h20M12 2c3 3 3 17 0 20M12 2c-3 3-3 17 0 20" fill="none" stroke-width="2" style="stroke:var(--gold)"/></svg>
        www.quietframe.com
      </li>
    </ul>
  </section>
</body>
</html>
```